Harrowgate Supply and Trade, LLC

Would like an e-commerce website started

coldbrook bearings website is a business that is almost exactly like ours...I like how in the front of the website...their lines flash across the bottom...I have attached our line card to add some of ours

we are tolk certified...I would like that to show...... attached logo

also attached our logo

```html
<!DOCTYPE html>
<html lang="en">
<head>
<meta charset="utf-8">
<title>Harrowgate Supply and Trade, LLC</title>
<link href="https://fonts.googleapis.com/css2?family=Montserrat:wght@400;500;600;700&display=swap" rel="stylesheet">
<style>
:root{
  --green:#5b9a22;
  --green-dark:#4a8219;
  --black:#050505;
  --ink:#222;
  --white:#fff;
  --brown-1:#8a6a4a;
  --brown-2:#5a4330;
}
*{box-sizing:border-box;margin:0;padding:0}
html,body{width:1200px;height:3613px;overflow:hidden}
body{position:relative;background:var(--white);font-family:'Montserrat',sans-serif;color:var(--ink)}
.abs{position:absolute}
svg.layer{position:absolute;left:0;top:0}
.topbar{left:0;top:0;width:1200px;height:52px;background:var(--black);color:var(--white);font-size:15px;font-weight:500}
.topbar span{position:absolute;top:16px;white-space:nowrap}
.nav{left:0;top:52px;width:1200px;height:65px;background:var(--white);border-bottom:1px solid #ddd}
.nav a{position:absolute;top:22px;font-size:15px;font-weight:500;color:var(--ink);text-decoration:none;transform:translateX(-50%);white-space:nowrap}
.nav .sep{position:absolute;top:0;width:1px;height:65px;background:#ccc}
.nav .quote{left:937px;top:0;width:175px;height:65px;background:var(--green);color:var(--white);transform:none;text-align:center;line-height:65px}
.brand{font-weight:600;text-align:center;line-height:1.15}
.brand-top{left:474px;top:0;width:252px;padding-top:62px;color:var(--ink);font-size:21px}
.hero-text{left:0;width:1200px;text-align:center;color:var(--white)}
.btn{position:absolute;background:var(--green);color:var(--white);font-weight:600;text-align:center;text-decoration:none;white-space:nowrap;clip-path:polygon(0 0,100% 0,100% 100%,12px 100%,0 calc(100% - 12px))}
h2.sec{position:absolute;color:var(--green);font-weight:600;font-size:34px;letter-spacing:0.5px;white-space:nowrap}
.body-text{font-size:17px;line-height:34px;color:var(--ink)}
.prod-list{left:112px;top:1654px;width:340px;height:344px;border-left:2px solid #fff}
.prod-list div{position:absolute;left:20px;font-size:21px;font-weight:600;color:var(--white);white-space:nowrap}
.prod-list .active{left:-2px;top:0;height:59px;background:var(--white);color:var(--black);padding:0 20px;line-height:59px;border-left:6px solid var(--green)}
.card{position:absolute;background:var(--white)}
.blog-card{position:absolute;top:2285px;width:255px;height:344px;background:var(--white);box-shadow:0 2px 8px rgba(0,0,0,.25);clip-path:polygon(0 0,100% 0,100% calc(100% - 30px),calc(100% - 30px) 100%,0 100%)}
.blog-card .ph{position:absolute;left:10px;top:14px;width:235px;height:140px}
.blog-card .date{position:absolute;left:26px;top:174px;font-size:16px;font-weight:600;color:var(--ink);white-space:nowrap}
.blog-card .date svg{vertical-align:-3px;margin-right:10px}
.blog-card p{position:absolute;left:26px;top:204px;width:215px;font-size:16px;line-height:34px}
.blog-card .btn{left:26px;top:283px;width:128px;height:35px;line-height:35px;font-size:15px}
.arrow{position:absolute;width:37px;height:37px;border-radius:50%}
.footer-text{color:var(--white);font-size:15px;font-weight:600;white-space:nowrap}
.ficon{position:absolute;width:42px;height:42px;border-radius:50%;background:var(--green)}
.fsep{position:absolute;top:3407px;width:1px;height:87px;background:#555}
</style>
</head>
<body>

<div class="abs topbar">
  <svg class="abs" style="left:78px;top:18px" width="15" height="15" viewBox="0 0 24 24"><path fill="#fff" d="M6.6 10.8a15 15 0 0 0 6.6 6.6l2.2-2.2c.3-.3.7-.4 1-.2 1.1.4 2.3.6 3.6.6.6 0 1 .4 1 1V20c0 .6-.4 1-1 1A17 17 0 0 1 3 4c0-.6.4-1 1-1h3.5c.6 0 1 .4 1 1 0 1.3.2 2.5.6 3.6.1.3 0 .7-.2 1z"/></svg>
  <span style="left:122px">555-201-4410</span>
  <span style="left:285px">555-201-4422</span>
  <svg class="abs" style="left:841px;top:19px" width="18" height="13" viewBox="0 0 18 13"><rect width="18" height="13" fill="#fff"/><path d="M0 0l9 7 9-7" stroke="#050505" stroke-width="1.5" fill="none"/></svg>
  <span style="left:885px">SALES@HARROWGATESUPPLY.COM</span>
</div>

<nav class="abs nav">
  <a href="#" style="left:107px">HOME</a>
  <span class="sep" style="left:163px"></span>
  <a href="#" style="left:240px">ABOUT US</a>
  <span class="sep" style="left:313px"></span>
  <a href="#" style="left:387px">SERVICES</a>
  <a href="#" style="left:829px">CONTACT US</a>
  <a href="#" class="quote">REQUEST A QUOTE</a>
</nav>

<svg class="layer" width="1200" height="740" style="top:0">
  <defs>
    <linearGradient id="heroGrad" x1="0" y1="0" x2="0" y2="1">
      <stop offset="0" stop-color="#3c332b"/>
      <stop offset="0.5" stop-color="#8a6a4a"/>
      <stop offset="1" stop-color="#5a4330"/>
    </linearGradient>
  </defs>
  <polygon role="img" aria-label="Warehouse aisle stacked with cardboard boxes" points="0,117 1200,117 1200,628 600,726 0,628" fill="url(#heroGrad)"/>
  <polygon points="0,628 600,712 1200,628 1200,632 600,738 0,632" fill="#5b9a22"/>
</svg>

<svg class="layer" width="1200" height="200" style="top:0">
  <polygon points="474,0 726,0 726,150 600,190 474,150" fill="#fff" style="filter:drop-shadow(0 2px 4px rgba(0,0,0,.3))"/>
</svg>
<div class="abs brand brand-top">HARROWGATE<br><span style="font-size:14px">SUPPLY AND TRADE, LLC</span></div>

<div class="abs hero-text" style="top:284px;font-size:29px;font-weight:500">WELCOME TO</div>
<div class="abs hero-text" style="top:336px;font-size:54px;font-weight:600;line-height:78px">HARROWGATE SUPPLY &amp;<br>TRADE LLC</div>
<a href="#" class="btn" style="left:493px;top:521px;width:212px;height:69px;line-height:69px;font-size:26px">GET STARTED</a>

<div class="abs" style="left:112px;top:868px;width:337px;height:486px;border:6px solid var(--green);border-top:none;border-right:none"></div>
<div class="abs" style="left:443px;top:1329px;width:6px;height:25px;background:var(--green)"></div>
<div class="abs" role="img" aria-label="Tool bag on a hardware store floor" style="left:135px;top:833px;width:461px;height:496px;background:linear-gradient(160deg,#9aa3ab,#6b7279 55%,#7a3a2a);clip-path:polygon(0 0,100% 0,100% 85%,87% 100%,0 100%)"></div>
<h2 class="sec" style="left:660px;top:864px">ABOUT US</h2>
<p class="abs body-text" style="left:660px;top:932px;width:430px">Sed ut perspiciatis unde omnis iste natus error sit voluptatem accusantium doloremque laudantium, totam rem aperiam, eaque ipsa quae ab illo inventore veritatis et quasi architecto beatae vitae dicta sunt explicabo. Nemo enim ipsam voluptatem quia voluptas sit aspernatur aut odit aut fugit, sed quia consequuntur magni dolores eos qui ratione voluptatem sequi nesciunt.</p>
<a href="#" class="btn" style="left:660px;top:1241px;width:220px;height:63px;line-height:63px;font-size:25px">LEARN MORE</a>

<svg class="layer" width="1200" height="3613">
  <polygon points="0,1423 600,1493 1200,1423 1200,2142 600,2071 0,2142" fill="#050505"/>
  <polygon points="0,1423 600,1482 1200,1423 1200,1425 600,1496 0,1425" fill="#5b9a22"/>
  <polygon points="0,2140 600,2068 1200,2140 1200,2142 600,2082 0,2142" fill="#5b9a22"/>
  <polygon points="0,3262 600,3155 1200,3262 1200,3613 0,3613" fill="#050505"/>
  <polygon points="0,3260 600,3150 1200,3260 1200,3263 600,3168 0,3263" fill="#5b9a22"/>
</svg>
<h2 class="sec" style="left:0;width:1200px;text-align:center;top:1564px">OUR PRODUCTS</h2>
<div class="abs prod-list">
  <div class="active">BEARING&nbsp; PULLERS</div>
  <div style="top:90px">BELTING</div>
  <div style="top:164px">CASTERS</div>
  <div style="top:239px">CONVEYOR COMPONENTS</div>
  <div style="top:312px">COUPLINGS</div>
</div>
<div class="card" style="left:475px;top:1654px;width:613px;height:333px">
  <div class="abs" role="img" aria-label="Polished steel ball and roller bearings" style="left:0;top:0;width:613px;height:211px;background:linear-gradient(135deg,#1d3550,#6f8fb0 45%,#24405f)"></div>
  <p class="abs" style="left:24px;top:238px;width:420px;font-size:15.5px;line-height:34px">Sed ut perspiciatis unde omnis iste natus error sit voluptatem accusantium doloremque laudantium</p>
  <a href="#" class="btn" style="left:462px;top:253px;width:129px;height:35px;line-height:35px;font-size:15px">READ MORE</a>
</div>

<h2 class="sec" style="left:0;width:1200px;text-align:center;top:2188px">LATEST BLOG POST</h2>
<svg class="arrow" style="left:91px;top:2441px" viewBox="0 0 37 37"><circle cx="18.5" cy="18.5" r="18.5" fill="#111"/><path d="M21 11l-7 7.5 7 7.5" stroke="#fff" stroke-width="3" fill="none"/></svg>
<svg class="arrow" style="left:1070px;top:2441px" viewBox="0 0 37 37"><circle cx="18.5" cy="18.5" r="18.5" fill="#5b9a22"/><path d="M16 11l7 7.5-7 7.5" stroke="#fff" stroke-width="3" fill="none"/></svg>

<div class="blog-card" style="left:177px">
  <div class="ph" role="img" aria-label="Metal cutting tool machining a part" style="background:linear-gradient(135deg,#1f3a55,#8aa3b8)"></div>
  <div class="date"><svg width="18" height="16" viewBox="0 0 18 16"><rect x="1" y="2" width="16" height="13" fill="none" stroke="#5b9a22" stroke-width="1.5"/><line x1="1" y1="6" x2="17" y2="6" stroke="#5b9a22" stroke-width="1.5"/></svg>9 JAN 2024</div>
  <p>Sed ut perspiciatis unde omnis iste natus error sit</p>
  <a href="#" class="btn">READ MORE</a>
</div>
<div class="blog-card" style="left:468px">
  <div class="ph" role="img" aria-label="Hands repairing a gearbox" style="background:linear-gradient(135deg,#3a3634,#8a7a6c)"></div>
  <div class="date"><svg width="18" height="16" viewBox="0 0 18 16"><rect x="1" y="2" width="16" height="13" fill="none" stroke="#5b9a22" stroke-width="1.5"/><line x1="1" y1="6" x2="17" y2="6" stroke="#5b9a22" stroke-width="1.5"/></svg>6 JAN 2024</div>
  <p>Sed ut perspiciatis unde omnis iste natus error sit</p>
  <a href="#" class="btn">READ MORE</a>
</div>
<div class="blog-card" style="left:758px">
  <div class="ph" role="img" aria-label="Hand picking a wrench from a tool wall" style="background:linear-gradient(135deg,#b9b4ad,#2b6f8f)"></div>
  <div class="date"><svg width="18" height="16" viewBox="0 0 18 16"><rect x="1" y="2" width="16" height="13" fill="none" stroke="#5b9a22" stroke-width="1.5"/><line x1="1" y1="6" x2="17" y2="6" stroke="#5b9a22" stroke-width="1.5"/></svg>12 JAN 2024</div>
  <p>Sed ut perspiciatis unde omnis iste natus error sit</p>
  <a href="#" class="btn">READ MORE</a>
</div>

<h2 class="sec" style="left:144px;top:2775px">TESTIMONIALS</h2>
<p class="abs body-text" style="left:144px;top:2843px;width:430px;font-size:16px">Sed ut perspiciatis unde omnis iste natus error sit voluptatem accusantium doloremque laudantium, totam rem aperiam, eaque ipsa</p>
<div class="abs" style="left:144px;top:2962px;color:var(--green);font-weight:600;font-size:18px">LOREM LIPSUM</div>
<svg class="abs" style="left:144px;top:3005px" width="80" height="14"><circle cx="7" cy="7" r="5.5" fill="#5b9a22"/><circle cx="37" cy="7" r="5.5" fill="#5b9a22"/><circle cx="66" cy="7" r="5.5" fill="#5b9a22"/></svg>
<div class="abs" style="left:813px;top:2752px;width:223px;height:318px;border:6px solid var(--green);border-left:none;border-top:none"></div>
<div class="abs" style="left:1030px;top:2752px;width:6px;height:20px;background:var(--green)"></div>
<div class="abs" role="img" aria-label="Portrait of a smiling customer" style="left:718px;top:2727px;width:304px;height:329px;background:linear-gradient(180deg,#f0c8a2,#e8b48c);clip-path:polygon(0 0,100% 0,100% 100%,12% 100%,0 88%)"></div>

<div class="abs brand" style="left:350px;top:3275px;width:260px;color:var(--white);font-size:28px">HARROWGATE<br><span style="font-size:17px">SUPPLY AND TRADE, LLC</span></div>
<div class="abs" role="img" aria-label="Tolk certification badge" style="left:690px;top:3281px;width:151px;height:60px;background:#fff;border-top:8px solid #5a2a8a"></div>

<div class="ficon" style="left:108px;top:3428px"><svg width="42" height="42" viewBox="0 0 42 42"><path fill="#fff" transform="translate(12 12) scale(.75)" d="M6.6 10.8a15 15 0 0 0 6.6 6.6l2.2-2.2c.3-.3.7-.4 1-.2 1.1.4 2.3.6 3.6.6.6 0 1 .4 1 1V20c0 .6-.4 1-1 1A17 17 0 0 1 3 4c0-.6.4-1 1-1h3.5c.6 0 1 .4 1 1 0 1.3.2 2.5.6 3.6.1.3 0 .7-.2 1z"/></svg></div>
<div class="abs footer-text" style="left:185px;top:3426px;line-height:44px">555-201-4410<br>555-201-4422</div>
<span class="fsep" style="left:346px"></span>
<div class="ficon" style="left:388px;top:3428px"><svg width="42" height="42" viewBox="0 0 42 42"><rect x="12" y="15" width="18" height="13" fill="#fff"/><path d="M12 15l9 7 9-7" stroke="#5b9a22" stroke-width="1.5" fill="none"/></svg></div>
<div class="abs footer-text" style="left:448px;top:3441px;font-size:14px">SALES@HARROWGATESUPPLY.COM</div>
<span class="fsep" style="left:707px"></span>
<div class="ficon" style="left:760px;top:3428px"><svg width="42" height="42" viewBox="0 0 42 42"><rect x="12" y="15" width="18" height="13" fill="#fff"/><path d="M12 15l9 7 9-7" stroke="#5b9a22" stroke-width="1.5" fill="none"/></svg></div>
<div class="abs footer-text" style="left:836px;top:3430px;line-height:38px">1207 FOUNDRY LN, ELMWOOD,<br>VA 23990</div>

<div class="abs footer-text" style="left:0;width:1200px;text-align:center;top:3548px;font-weight:500">@2024 COPYRIGHTS - ALL RIGHTS RESERVED</div>
</body>
</html>
```